Business Card for Lantern Reach

Please design a Modern Business card for a Online Marketing Company

Website: http://www.lanternreach-example.com.au

Please do NOT include physical address in design.

```html
<!DOCTYPE html>
<html lang="en">
<head>
<meta charset="utf-8">
<title>Lantern Reach – Business Card</title>
<link rel="stylesheet" href="https://fonts.googleapis.com/css2?family=Roboto:wght@700;900&family=Open+Sans:wght@400;600&display=swap">
<style>
  :root {
    --page-bg: #ece9e6;
    --card-white: #ffffff;
    --brand-red: #c20f1f;
    --brand-orange: #f08a1c;
    --ink: #1e1e1e;
    --on-red: #ffffff;
    --icon-red: #b3121f;
  }
  * { box-sizing: border-box; margin: 0; padding: 0; }
  html, body {
    width: 1200px; height: 466px; overflow: hidden;
    background: var(--page-bg);
  }
  .canvas { position: relative; width: 1200px; height: 466px; }
  .card {
    position: absolute; top: 83px;
    width: 520px; height: 300px;
    border-radius: 28px;
    overflow: hidden;
    box-shadow: 0 6px 18px rgba(0,0,0,0.18);
  }
  .card--front { left: 40px; background: var(--card-white); }
  .card--back  { left: 640px; background: var(--brand-red); color: var(--on-red); }

  /* front */
  .brand { position: absolute; left: 40px; top: 52px; }
  .brand__row { display: flex; align-items: center; gap: 12px; }
  .brand__square {
    width: 34px; height: 34px; border-radius: 6px;
    background: var(--brand-orange); flex: none;
  }
  .brand__name {
    font-family: "Roboto", Arial, sans-serif; font-weight: 700;
    font-size: 22px; letter-spacing: 0.2px; color: var(--brand-red); line-height: 1;
  }
  .brand__tagline {
    font-family: "Roboto", Arial, sans-serif; font-weight: 700;
    font-size: 11px; color: var(--ink); margin-top: 2px; padding-left: 46px;
  }
  .person { position: absolute; left: 40px; top: 158px; }
  .person__name {
    font-family: "Open Sans", Arial, sans-serif; font-weight: 600;
    font-size: 18px; color: var(--brand-red); line-height: 1.1;
  }
  .person__title {
    font-family: "Open Sans", Arial, sans-serif; font-weight: 400;
    font-size: 13px; color: var(--brand-orange); margin-top: 2px;
  }
  .contact { position: absolute; left: 40px; top: 218px; list-style: none; }
  .contact__item {
    display: flex; align-items: center; gap: 8px;
    font-family: "Open Sans", Arial, sans-serif; font-size: 12.5px;
    color: var(--ink); line-height: 20px;
  }
  .contact__icon { width: 12px; height: 12px; flex: none; }

  /* back */
  .back__content { position: absolute; left: 0; right: 0; top: 96px; text-align: center; }
  .back__name {
    font-family: "Roboto", Arial, sans-serif; font-weight: 700;
    font-size: 40px; letter-spacing: 0.5px; line-height: 1;
  }
  .back__tagline {
    font-family: "Roboto", Arial, sans-serif; font-weight: 700;
    font-size: 19px; margin-top: 6px;
  }
  .back__web {
    position: absolute; left: 0; right: 0; bottom: 46px; text-align: center;
    font-family: "Open Sans", Arial, sans-serif; font-size: 16px; letter-spacing: 1px;
  }
</style>
</head>
<body>
<main class="canvas">

  <section class="card card--front" aria-label="Card front">
    <div class="brand">
      <div class="brand__row">
        <span class="brand__square" aria-hidden="true"></span>
        <span class="brand__name">LANTERN REACH</span>
      </div>
      <p class="brand__tagline">Be seen online - Grow online</p>
    </div>

    <div class="person">
      <p class="person__name">Your Name</p>
      <p class="person__title">Title</p>
    </div>

    <ul class="contact">
      <li class="contact__item">
        <svg class="contact__icon" viewBox="0 0 12 12" aria-hidden="true">
          <path fill="var(--icon-red)" d="M2.6 0.8l1.8 2.2-1 1.2c0.6 1.5 1.8 2.7 3.3 3.3l1.2-1 2.2 1.8-1.1 2C5 10 2 7 1.4 1.9z"/>
        </svg>
        0400 123 456
      </li>
      <li class="contact__item">
        <svg class="contact__icon" viewBox="0 0 12 12" aria-hidden="true">
          <rect x="0.5" y="2.5" width="11" height="7.5" rx="1.2" fill="var(--icon-red)"/>
          <path d="M1.2 3.2L6 6.8l4.8-3.6" fill="none" stroke="#fff" stroke-width="1"/>
        </svg>
        hello@lanternreach-example.com.au
      </li>
      <li class="contact__item">
        <svg class="contact__icon" viewBox="0 0 12 12" aria-hidden="true">
          <circle cx="6" cy="6" r="5.5" fill="var(--icon-red)"/>
          <path d="M0.8 6h10.4M6 0.6v10.8" fill="none" stroke="#fff" stroke-width="0.7"/>
          <ellipse cx="6" cy="6" rx="2.4" ry="5.4" fill="none" stroke="#fff" stroke-width="0.7"/>
        </svg>
        www.lanternreach-example.com.au
      </li>
    </ul>
  </section>

  <section class="card card--back" aria-label="Card back">
    <div class="back__content">
      <h1 class="back__name">LANTERN REACH</h1>
      <p class="back__tagline">Be seen online - Grow online</p>
    </div>
    <p class="back__web">www.lanternreach-example.com.au</p>
  </section>

</main>
</body>
</html>
```